Quorva - corporate Business Card

We need a good look and innovative business card for a new start up company based in Los Angeles called "Quorva". We are in a payment business, including payment card, app, and ewallet. We are expert in online payment and Card not present (CNP) transaction.
We need an innovative, modern business card.

Our logo font is Aero Matics

Target Market(s)

Startup - Bank - Online Payment - Card Manufacturing

Industry/Entity Type

Startup

Contact Information for Business Card

phone: 555 014 7396 - Address: 4172 Marlowe blvd, Linden Heights, CA 90299

Requirements
Must have
• Message: innovative, professional, expert, high tech, trust, online payment expert, security
Nice to have
• no comment
Should not have
• no Comment

```html
<!DOCTYPE html>
<html lang="en">
<head>
<meta charset="utf-8">
<title>Quorva – Business Card</title>
<link href="https://fonts.googleapis.com/css2?family=Lato:wght@400;700&display=swap" rel="stylesheet">
<style>
  :root {
    --brand-red: #b41e2d;
    --brand-red-soft: rgba(255, 255, 255, 0.2);
    --paper: #ffffff;
    --ink: #1d1d1d;
    --stage: #ececec;
  }
  * { margin: 0; padding: 0; box-sizing: border-box; }
  html, body {
    width: 1200px; height: 586px; overflow: hidden;
    background: var(--stage);
    font-family: 'Lato', sans-serif;
  }
  .canvas { position: relative; width: 1200px; height: 586px; }
  .card {
    position: absolute; top: 129px;
    width: 502px; height: 300px; overflow: hidden;
  }
  /* Front */
  .card-front { left: 61px; background: var(--brand-red); }
  .front-disc {
    position: absolute; left: 258px; top: 23px;
    width: 260px; height: 260px; border-radius: 50%;
    background: var(--brand-red-soft);
  }
  .front-name {
    position: absolute; left: 30px; top: 215px;
    font-size: 40px; font-weight: 700; color: var(--paper); line-height: 1;
  }
  .front-web {
    position: absolute; left: 32px; top: 262px;
    font-size: 11px; font-weight: 700; letter-spacing: 3.2px; color: var(--paper);
  }
  /* Back */
  .card-back { left: 619px; background: var(--paper); }
  .brand-lockup {
    position: absolute; left: 145px; top: 33px;
    display: flex; align-items: center; gap: 10px;
  }
  .brand-dot { width: 64px; height: 64px; border-radius: 50%; background: var(--brand-red); }
  .brand-name { font-size: 45px; font-weight: 700; color: var(--brand-red); line-height: 1; }
  .person {
    position: absolute; right: 294px; top: 168px; text-align: right;
  }
  .person-name { font-size: 16px; font-weight: 700; color: var(--brand-red); }
  .person-role { font-size: 11px; color: var(--ink); margin-top: 5px; }
  .divider {
    position: absolute; left: 235px; top: 142px; width: 2px; height: 106px;
    background: linear-gradient(to bottom, rgba(180,30,45,0), var(--brand-red) 40%, var(--brand-red) 60%, rgba(180,30,45,0));
  }
  .contact { position: absolute; left: 262px; top: 164px; list-style: none; }
  .contact li {
    display: flex; align-items: center; gap: 8px;
    height: 25px; font-size: 12px; color: var(--ink);
  }
  .contact svg { width: 17px; height: 17px; flex: none; }
  .address-band {
    position: absolute; left: 0; bottom: 0; width: 100%; height: 30px;
    background: var(--brand-red); color: var(--paper);
    display: flex; align-items: center; justify-content: center;
    font-size: 12px; font-weight: 700;
  }
</style>
</head>
<body>
<main class="canvas">
  <section class="card card-front" aria-label="Card front">
    <div class="front-disc" aria-hidden="true"></div>
    <p class="front-name">quorva</p>
    <p class="front-web">www.quorvapay.com</p>
  </section>

  <section class="card card-back" aria-label="Card back">
    <div class="brand-lockup">
      <span class="brand-dot" aria-hidden="true"></span>
      <span class="brand-name">quorva</span>
    </div>

    <div class="person">
      <p class="person-name">Marcus Delaney</p>
      <p class="person-role">Owner &amp; Founder</p>
    </div>

    <div class="divider" aria-hidden="true"></div>

    <ul class="contact">
      <li>
        <svg viewBox="0 0 20 20" aria-hidden="true">
          <circle cx="10" cy="10" r="10" fill="#b41e2d"/>
          <path d="M6 7.5c1-1.5 7-1.5 8 0l-.6 1.4-1.8-.4-.2-1h-2.8l-.2 1-1.8.4z" fill="#fff"/>
          <rect x="7" y="9.5" width="6" height="4" rx="0.8" fill="#fff"/>
        </svg>
        (555) 014-7396
      </li>
      <li>
        <svg viewBox="0 0 20 20" aria-hidden="true">
          <circle cx="10" cy="10" r="10" fill="#b41e2d"/>
          <rect x="5.5" y="6.5" width="9" height="7" fill="#fff"/>
          <path d="M5.5 6.5l4.5 4 4.5-4" fill="none" stroke="#b41e2d" stroke-width="1"/>
        </svg>
        MarcusD@quorvapay.com
      </li>
    </ul>

    <div class="address-band">4172 Marlowe blvd, Linden Heights, CA 90299</div>
  </section>
</main>
</body>
</html>
```